WE ARE BRIGHT SPARROW, building a full website with ecommerce

requirements:
CODED FOR SITEQUILL
ONLINE STORE FUNCTION WITH E-COMMERCE USING TRADEBLOOM
PAGEWAVE AND PICTOLANE LINKS

I need a website design for my organization, WE ARE BRIGHT SPARROW, a global empowerment movement elevating woman, and the world. The site's home page should reflect our mission, to empower women. It should have a strong, empowering feel, with minimalistic design.
Please see www.lunavelto.com and http://www.corvenhal.co/ for an inspiration on layout and feel.

**PLEASE SEE ATTACHMENT "LOGO MOCK UP" FOR LOGO. THIS IS NOT THE FINAL VECTOR FILE, BUT THIS LOOKS THE SAME AS THE FINAL LOGO.

HOME PAGE:
The first section of the home page should include a background image with our logo center.

You should include the following links to pages at the top right of the page:
MISSION
MANTRA
ARMOR
MEET BS (I would like "bs" to be our logo)
pagewave and pictolane links

As you scroll down the page, you should see the following sections, which correlate to the links to pages as written above. **SEE ATTACHED SKETCH "HOMEPAGE LAYOUT IDEA" FOR REFERENCE**

WHO WE ARE (correlates to the link Mission)

OUR MANTRA (correlates to the link Mantra)

OUR ARMOR (correlates to the link The Shirt)
(This is where we will sell a shirt (and other apparel) and need the e-commerce function)

MEET BRIGHT SPARROWS (correlates to the link Meet BS)

SHOW OFF YOUR SUPER POWERS (correlates to the pagewave and pictolane)

FEATURED BRIGHT SPARROW (no link on top right of page)

On the homepage, for each of the above sections, as you scroll down there should be an image, either in the background or framed, next to the title (WHO WE ARE, for example), as well as one sentence of small text explaining the title. The title (WHO WE ARE) and the one sentence should link to a page (ie WHO WE ARE + the one sentence links to the MISSION page). ** SEE ATTACHED SKETCH "HOMEPAGE SECTION IDEAS" FOR REFERENCE**

**PLEASE SEE ATTACHMENT "WEBSITE TITLE IDEAS" FOR A STARTING PLACE OF THE LOOK. These don't have to be exact, but they give you an idea of what I'm looking for.

**FONTS TYPOLD EXTRA BOLD AND TYPOLD BOOK 500 (WHICH SHOULD BE BOLDED MANUALLY) ARE ATTACHED**

Target Market(s)

Women, mainly in US

Industry/Entity Type

Social

Coding

Coded - Design and coding required

Number of Pages Required

5+ page

Font styles to use
Other font styles liked:
• Typol Extra Bold

Requirements
Must have
• CODED FOR SITEQUILL
• ONLINE STORE FUNCTION WITH E-COMMERCE USING TRADEBLOOM
• PAGEWAVE AND PICTOLANE LINKS
• Typold Extra Bold and Typold Book 500, attached
• please see description for all requirements
Nice to have
• please see description for all ideas
Should not have

```html
<!DOCTYPE html>
<html lang="en">
<head>
<meta charset="utf-8">
<title>We Are Bright Sparrow</title>
<link href="https://fonts.googleapis.com/css2?family=Montserrat:wght@300;400;600;700;800&family=Open+Sans:wght@400;600&display=swap" rel="stylesheet">
<style>
:root{
  --white:#ffffff;
  --ink:#1f1f1f;
  --grey:#6d6d6d;
  --line:#e4e4e4;
  --purple:#4b1877;
  --pagewave:#3b5ba5;
  --pictolane-a:#f0902c;
  --pictolane-b:#c2307f;
  --shirt-red:#e5252a;
  --shirt-green:#22e04a;
  --shade:rgba(20,20,25,.45);
}
*{margin:0;padding:0;box-sizing:border-box}
html,body{width:1200px;height:3543px;overflow:hidden}
body{position:relative;background:var(--white);font-family:"Open Sans",Arial,sans-serif;color:var(--ink)}
.head{font-family:"Montserrat",Arial,sans-serif}
.abs{position:absolute}

/* header */
.site-header{position:absolute;left:0;top:0;width:1200px;height:90px;background:var(--white);display:flex;align-items:center;justify-content:space-between;padding:0 98px}
.brand{display:flex;align-items:center;gap:12px;font-family:"Montserrat",sans-serif;font-weight:800;font-size:15px;line-height:17px;letter-spacing:.5px}
.brand-mark{width:26px;height:26px;border:3px solid var(--ink);transform:rotate(45deg)}
.nav{display:flex;align-items:center;gap:30px;font-family:"Montserrat",sans-serif;font-size:14px;letter-spacing:1.5px;color:#333}
.nav .dot{display:inline-block;width:14px;height:14px;border-radius:50%;vertical-align:-2px;margin-right:6px}
.dot.pw{background:var(--pagewave)}
.dot.pl{background:linear-gradient(135deg,var(--pictolane-a),var(--pictolane-b))}
.nav .sq{display:inline-block;width:10px;height:10px;border:2px solid #333;transform:rotate(45deg);margin-left:6px}

/* sections */
.band{position:absolute;left:0;width:1200px;overflow:hidden}
.photo{position:absolute;inset:0}
.shade{position:absolute;inset:0;background:var(--shade)}
.divider{position:absolute;left:551px;width:98px;height:98px;margin-top:-49px;background:var(--white);border:6px solid #ececec;transform:rotate(45deg);z-index:5}

.title{position:absolute;color:var(--white);font-family:"Montserrat",sans-serif;text-transform:uppercase;line-height:.98}
.title .mark{position:absolute;left:-112px;top:12px;width:72px;height:72px;border:10px solid var(--white);transform:rotate(45deg)}
.title .b{font-weight:800}
.title .l{font-weight:300}
.title .lg{font-size:58px}
.title .sm{font-size:32px}
.blurb{position:absolute;width:480px;color:var(--white);font-size:13px;line-height:30px}

/* hero */
.hero-mark{position:absolute;left:558px;top:210px;width:84px;height:84px;border:11px solid var(--white);transform:rotate(45deg)}
.hero-title{position:absolute;left:0;top:325px;width:1200px;text-align:center;color:var(--white);font-family:"Montserrat",sans-serif}
.hero-title h1{font-size:33px;font-weight:700;letter-spacing:1px}
.hero-title p{font-size:31px;font-weight:400;margin-top:14px;letter-spacing:.5px}
.signup{position:absolute;left:350px;top:462px;display:flex;height:50px}
.signup .field{width:362px;border:2px solid var(--white);border-right:0;color:var(--white);font-size:15px;padding:13px 16px;background:rgba(0,0,0,.25)}
.signup .go{width:138px;background:var(--white);color:var(--ink);font-family:"Montserrat",sans-serif;font-weight:800;font-size:16px;display:flex;align-items:center;justify-content:center}

/* mission band */
.mission{background:var(--purple);color:var(--white);text-align:center}
.mission h2{font-family:"Montserrat",sans-serif;font-weight:700;font-size:22px;letter-spacing:1.5px;line-height:52px;margin-top:100px}
.fly{display:inline-flex;align-items:center;gap:10px;margin-top:40px;font-family:"Montserrat",sans-serif;font-weight:800;font-size:24px;line-height:1}
.fly i{width:22px;height:22px;border:4px solid var(--white);transform:rotate(45deg)}

/* armor */
.product{position:absolute;width:214px;height:214px;transform:rotate(45deg);background:var(--white)}
.product-shot{position:absolute;width:122px;height:110px;border-radius:6px}
.product-name{position:absolute;width:220px;text-align:center;font-family:"Montserrat",sans-serif;font-weight:700;font-size:12px;color:var(--ink)}
.cart{position:absolute;width:60px;height:60px;background:var(--ink);transform:rotate(45deg)}
.cart-icon{position:absolute}

/* social */
.social{position:absolute;width:110px;height:110px;transform:rotate(45deg)}
.social-name{position:absolute;width:160px;text-align:center;color:var(--white);font-family:"Montserrat",sans-serif;font-weight:700;font-size:15px;letter-spacing:1px}

/* footer */
.footer{position:absolute;left:0;top:3217px;width:1200px;height:326px;background:var(--white)}
.col{position:absolute;top:93px}
.col h3{font-family:"Montserrat",sans-serif;font-weight:700;font-size:15px;letter-spacing:.5px;color:var(--ink);margin-bottom:18px}
.col li{list-style:none;font-size:12px;color:var(--grey);line-height:28px}
.col li::before{content:"›";margin-right:8px;color:var(--ink)}
.contact-row{display:flex;align-items:center;gap:14px;font-size:12px;color:var(--grey);line-height:40px}
.follow{display:flex;gap:14px;margin-top:4px}
.follow span{display:flex;align-items:center;gap:6px;font-size:11px;font-family:"Montserrat",sans-serif;font-weight:700;color:var(--ink)}
.follow i{width:16px;height:16px;border-radius:50%}
.rule{position:absolute;left:98px;top:253px;width:1004px;height:1px;background:var(--line)}
.copy{position:absolute;left:0;top:280px;width:1200px;text-align:center;font-size:11px;color:var(--grey)}
</style>
</head>
<body>

<header class="site-header">
  <div class="brand"><span class="brand-mark"></span><span>WE ARE<br>BRIGHT SPARROW</span></div>
  <nav class="nav">
    <span>MISSION</span><span>MANTRA</span><span>ARMOR</span>
    <span>MEET BS<span class="sq"></span></span>
    <span><span class="dot pw"></span>PAGEWAVE</span>
    <span><span class="dot pl"></span>PICTOLANE</span>
  </nav>
</header>

<section class="band" style="top:90px;height:578px">
  <div class="photo" role="img" aria-label="Photo of a woman raising her arms in triumph in a bright office" style="background:linear-gradient(100deg,#6f6a66 0%,#b8a792 45%,#d8b47a 75%,#c58a4a 100%)"></div>
  <div class="shade" style="background:rgba(20,20,25,.35)"></div>
  <div class="hero-mark"></div>
  <div class="hero-title"><h1>WE ARE BRIGHT SPARROW</h1><p>AND I WILL CONQUER THE WORLD</p></div>
  <div class="signup"><div class="field">hello@brightsparrow.org</div><div class="go">LET'S FLY</div></div>
</section>

<section class="band mission" style="top:668px;height:372px">
  <h2>WE ARE BRIGHT SPARROW IS A GLOBAL EMPOWERMENT MOVEMENT<br>ELEVATING WOMEN... AND THE WORLD.</h2>
  <div class="fly"><i></i><span>LET'S FLY</span></div>
</section>

<section class="band" style="top:1046px;height:364px">
  <div class="photo" role="img" aria-label="Photo of joyful women cheering together" style="background:linear-gradient(90deg,#3f4f6a 0%,#8b7f78 40%,#a59c92 70%,#bdb4a8 100%)"></div>
  <div class="shade"></div>
  <div class="title" style="left:322px;top:95px"><span class="mark"></span><span class="l lg">WHO</span><br><span class="l lg">WE</span><br><span class="b lg">ARE</span></div>
  <p class="blurb" style="left:640px;top:118px">All the Lorem Ipsum generators on the Internet tend to repeat predefined chunks as necessary, making this the first true generator on the Internet. It uses a dictionary of over 200 Latin words, combined with a handful of model sentence structures, to generate reasonable.</p>
</section>

<section class="band" style="top:1417px;height:331px">
  <div class="photo" role="img" aria-label="Photo of a smiling businesswoman in a bright office" style="background:linear-gradient(90deg,#9a9b98 0%,#c4bdb4 40%,#b3b5b3 70%,#8d9496 100%)"></div>
  <div class="shade"></div>
  <p class="blurb" style="left:100px;top:108px">All the Lorem Ipsum generators on the Internet tend to repeat predefined chunks as necessary, making this the first true generator on the Internet. It uses a dictionary of over 200 Latin words, combined with a handful of model sentence structures, to generate reasonable.</p>
  <div class="title" style="left:808px;top:105px"><span class="mark"></span><span class="b lg">OUR</span><br><span class="l lg">MANTRA</span></div>
</section>

<section class="band" style="top:1755px;height:340px">
  <div class="photo" role="img" aria-label="Photo of a smiling woman with colleagues behind her" style="background:linear-gradient(90deg,#6f6560 0%,#8a6e5e 45%,#a49a92 75%,#c8c4be 100%)"></div>
  <div class="shade"></div>
  <div class="title" style="left:275px;top:110px"><span class="mark"></span><span class="b sm">MEET</span><br><span class="l lg" style="font-size:48px">BRIGHT</span><br><span class="b lg" style="font-size:48px">SPARROWS</span></div>
  <p class="blurb" style="left:640px;top:118px">All the Lorem Ipsum generators on the Internet tend to repeat predefined chunks as necessary, making this the first true generator on the Internet. It uses a dictionary of over 200 Latin words, combined with a handful of model sentence structures, to generate reasonable.</p>
</section>

<section class="band" style="top:2102px;height:438px">
  <div class="photo" role="img" aria-label="Photo of a confident smiling woman in an office" style="background:linear-gradient(90deg,#7c8580 0%,#9ea6a0 40%,#a08a78 70%,#8c857e 100%)"></div>
  <div class="shade"></div>
  <div class="product" style="left:143px;top:105px"></div>
  <div class="product-shot" role="img" aria-label="Red Bright Sparrow t-shirt" style="left:189px;top:140px;background:var(--shirt-red)"></div>
  <div class="product-name" style="left:140px;top:268px">Bright Sparrow T-shirt</div>
  <div class="cart" style="left:220px;top:300px"></div>
  <svg class="cart-icon" style="left:239px;top:318px" width="22" height="22" viewBox="0 0 22 22" fill="none" stroke="#fff" stroke-width="2"><path d="M3 5h16l-2 10H5z"/><path d="M7 5a4 4 0 0 1 8 0"/></svg>
  <div class="product" style="left:443px;top:105px"></div>
  <div class="product-shot" role="img" aria-label="Green Bright Sparrow t-shirt" style="left:489px;top:140px;background:var(--shirt-green)"></div>
  <div class="product-name" style="left:440px;top:268px">Bright Sparrow T-shirt</div>
  <div class="cart" style="left:520px;top:300px"></div>
  <svg class="cart-icon" style="left:539px;top:318px" width="22" height="22" viewBox="0 0 22 22" fill="none" stroke="#fff" stroke-width="2"><path d="M3 5h16l-2 10H5z"/><path d="M7 5a4 4 0 0 1 8 0"/></svg>
  <div class="title" style="left:875px;top:165px"><span class="mark"></span><span class="b lg">OUR</span><br><span class="l lg">ARMOR</span></div>
</section>

<section class="band" style="top:2546px;height:331px">
  <div class="photo" role="img" aria-label="Photo of a businesswoman in a red jacket in a bright hallway" style="background:linear-gradient(90deg,#b9a9a4 0%,#d6d6d6 25%,#c7cacc 60%,#aeb3b6 100%)"></div>
  <div class="shade" style="background:rgba(20,20,25,.3)"></div>
  <div class="title" style="left:265px;top:120px"><span class="mark"></span><span class="b" style="font-size:26px">SHOW OFF YOUR</span><br><span class="l lg" style="font-size:48px">SUPER</span><br><span class="b lg" style="font-size:48px">POWERS</span></div>
  <div class="social" style="left:753px;top:110px;background:var(--pagewave)"></div>
  <div class="social-name" style="left:728px;top:155px">PAGEWAVE</div>
  <div class="social" style="left:920px;top:110px;background:linear-gradient(135deg,var(--pictolane-a),var(--pictolane-b))"></div>
  <div class="social-name" style="left:895px;top:155px">PICTOLANE</div>
</section>

<section class="band" style="top:2884px;height:333px">
  <div class="photo" role="img" aria-label="Photo of three smiling women standing close together" style="background:linear-gradient(90deg,#8a6e60 0%,#a88b78 40%,#9c8a7e 70%,#c6bcb2 100%)"></div>
  <div class="shade"></div>
  <p class="blurb" style="left:100px;top:120px">All the Lorem Ipsum generators on the Internet tend to repeat predefined chunks as necessary, making this the first true generator on the Internet. It uses a dictionary of over 200 Latin words, combined with a handful of model sentence structures, to generate reasonable.</p>
  <div class="title" style="left:862px;top:110px"><span class="mark"></span><span class="b sm">FEATURED</span><br><span class="l lg" style="font-size:48px">BRIGHT</span><br><span class="b lg" style="font-size:48px">SPARROW</span></div>
</section>

<div class="divider" style="top:668px"></div>
<div class="divider" style="top:1043px"></div>
<div class="divider" style="top:1413px"></div>
<div class="divider" style="top:1751px"></div>
<div class="divider" style="top:2098px"></div>
<div class="divider" style="top:2543px"></div>
<div class="divider" style="top:2880px"></div>
<div class="divider" style="top:3217px"></div>

<footer class="footer">
  <div class="col" style="left:98px"><h3>QUICK LINKS</h3><ul><li>Mission</li><li>Mantra</li><li>Armor</li></ul></div>
  <div class="col" style="left:380px"><h3>OTHER LINKS</h3><ul><li>Meet BS</li><li>FAQs</li><li>Terms &amp; Conditions</li></ul></div>
  <div class="col" style="left:655px"><h3>CONTACT US</h3>
    <div class="contact-row"><svg width="14" height="14" viewBox="0 0 24 24" fill="#888"><path d="M6.6 10.8a15 15 0 0 0 6.6 6.6l2.2-2.2a1 1 0 0 1 1-.25 11.4 11.4 0 0 0 3.6.57 1 1 0 0 1 1 1V20a1 1 0 0 1-1 1A17 17 0 0 1 3 4a1 1 0 0 1 1-1h3.5a1 1 0 0 1 1 1c0 1.25.2 2.45.57 3.57a1 1 0 0 1-.25 1z"/></svg>(+1) 555 014 2290</div>
    <div class="contact-row"><svg width="14" height="12" viewBox="0 0 24 20" fill="none" stroke="#888" stroke-width="2"><rect x="1" y="1" width="22" height="18"/><path d="M1 1l11 9 11-9"/></svg>info@brightsparrow.org</div>
  </div>
  <div class="col" style="left:990px"><h3>FOLLOW US</h3>
    <div class="follow"><span><i style="background:var(--pagewave)"></i>PAGEWAVE</span></div>
    <div class="follow" style="margin-top:10px"><span><i style="background:var(--pictolane-b)"></i>PICTOLANE</span></div>
  </div>
  <div class="rule"></div>
  <p class="copy">© Copyright 2017 Bright Sparrow. All Rights Reserved</p>
</footer>

</body>
</html>
```